Business Card Design

We need a business card designed for our new company. Prefer a black card with white logo & writing.

Contact Information for Business Card

Ted Galloway, address: 7-4812 Fernhollow Road, Abbotsford, BC, V3K 8R2, Office Phone: 604-712-3390, Cell: 604-947-2164, Email: ted@resinworkshub.ca

Colors

Designer to choose only greyscale colors for use in the design.

```html
<!DOCTYPE html>
<html lang="en">
<head>
<meta charset="utf-8">
<title>Resinworks Hub – Business Card</title>
<link rel="stylesheet" href="https://fonts.googleapis.com/css2?family=Montserrat:wght@400;800&display=swap">
<style>
  :root {
    --backdrop: #2b2b2b;
    --card: #121212;
    --ink: #ffffff;
    --ink-soft: #e6e6e6;
    --rule: #bdbdbd;
  }
  * { margin: 0; padding: 0; box-sizing: border-box; }
  html, body {
    width: 1200px;
    height: 900px;
    overflow: hidden;
    background: var(--backdrop);
    font-family: "Montserrat", sans-serif;
  }
  .sheet {
    width: 1200px;
    height: 900px;
    display: flex;
    flex-direction: column;
    align-items: center;
    justify-content: center;
    gap: 40px;
  }
  .card {
    position: relative;
    width: 700px;
    height: 400px;
    background: var(--card);
    color: var(--ink);
    box-shadow: 0 10px 30px rgba(0,0,0,.45);
    overflow: hidden;
  }

  /* Front */
  .card--front {
    display: flex;
    align-items: center;
    justify-content: center;
  }
  .wordmark {
    font-weight: 800;
    color: var(--ink);
    text-transform: uppercase;
    line-height: 1;
    letter-spacing: 0.02em;
  }
  .card--front .wordmark { font-size: 58px; }

  /* Back */
  .accent-bar {
    position: absolute;
    width: 18px;
    background: var(--ink);
  }
  .accent-bar--top { left: 40px; top: 0; height: 150px; }
  .accent-bar--bottom { right: 40px; bottom: 0; height: 150px; }

  .card--back .brand {
    position: absolute;
    left: 80px;
    top: 0;
    width: 260px;
    height: 400px;
    display: flex;
    align-items: center;
    justify-content: center;
  }
  .card--back .wordmark { font-size: 30px; text-align: center; }

  .divider {
    position: absolute;
    left: 360px;
    top: 110px;
    width: 1px;
    height: 180px;
    background: var(--rule);
  }

  .contact {
    position: absolute;
    left: 392px;
    top: 96px;
  }
  .contact__name {
    font-weight: 800;
    font-size: 26px;
    margin-bottom: 16px;
    letter-spacing: 0.01em;
  }
  .contact__list { list-style: none; }
  .contact__item {
    display: flex;
    align-items: center;
    gap: 8px;
    font-size: 16px;
    line-height: 26px;
    color: var(--ink-soft);
  }
  .contact__item svg { width: 14px; height: 14px; fill: var(--ink-soft); flex: none; }
  .contact__address {
    margin-top: 12px;
    font-size: 16px;
    line-height: 24px;
    color: var(--ink-soft);
    font-style: normal;
  }
</style>
</head>
<body>
<main class="sheet">

  <section class="card card--front" aria-label="Card front">
    <div class="wordmark">Resinworks Hub</div>
  </section>

  <section class="card card--back" aria-label="Card back">
    <span class="accent-bar accent-bar--top"></span>
    <span class="accent-bar accent-bar--bottom"></span>

    <div class="brand">
      <div class="wordmark">Resinworks<br>Hub</div>
    </div>

    <span class="divider"></span>

    <div class="contact">
      <h1 class="contact__name">Ted Galloway</h1>
      <ul class="contact__list">
        <li class="contact__item">
          <svg viewBox="0 0 24 24" aria-hidden="true"><path d="M6.6 10.8a15.1 15.1 0 0 0 6.6 6.6l2.2-2.2a1 1 0 0 1 1-.25 11.4 11.4 0 0 0 3.6.57 1 1 0 0 1 1 1V20a1 1 0 0 1-1 1A17 17 0 0 1 3 4a1 1 0 0 1 1-1h3.5a1 1 0 0 1 1 1c0 1.25.2 2.45.57 3.6a1 1 0 0 1-.25 1z"/></svg>
          604-712-3390
        </li>
        <li class="contact__item">
          <svg viewBox="0 0 24 24" aria-hidden="true"><path d="M7 1h10a2 2 0 0 1 2 2v18a2 2 0 0 1-2 2H7a2 2 0 0 1-2-2V3a2 2 0 0 1 2-2zm0 3v14h10V4zm5 15.5a1.2 1.2 0 1 0 0 2.4 1.2 1.2 0 0 0 0-2.4z"/></svg>
          604-947-2164
        </li>
        <li class="contact__item">
          <svg viewBox="0 0 24 24" aria-hidden="true"><path d="M3 5h18a1 1 0 0 1 1 1v12a1 1 0 0 1-1 1H3a1 1 0 0 1-1-1V6a1 1 0 0 1 1-1zm1 2.2V17h16V7.2l-8 5.3z M5 7l7 4.6L19 7z"/></svg>
          ted@resinworkshub.ca
        </li>
      </ul>
      <address class="contact__address">
        7-4812 Fernhollow Road,<br>
        Abbotsford, BC, V3K 8R2
      </address>
    </div>
  </section>

</main>
</body>
</html>
```